Open Harbor book needs a cover design

I need a front and back cover design that demonstrates a strong sense of possibility that trust can be repaired even if things look bleak. Repairing trust is difficult, but this book is full of wisdom, proven strategies, and doctoral research to help people strengthen relationships and improve trust. It can help any group: business, nonprofit, education, service. Showing diversity of groups and people is very important. For the cover title, there should be a play on words: "Open Harbor: Is it? Within Reach" should have the words "is it?" crossed out and the words "It IS! should be replaced there in a striking way. Perhaps in red ink. For publishing purposes, book will be titled Open Harbor: It IS Within Reach! Please see the attachment for an example. The book layout is approximately 260 pages.

A business self-help book, but the target is any person in a group that feels they have lost trust in each other. It can be just a normal person struggling in a volunteer group they are a part of, or a supervisor whose group is not working well together. It can be a leader who just wants their group to be stronger.

Business Management

• Allise - I believe is being used on the interior of the book for the title page and headings

• Show hope and possibility in the midst of difficulty. Must have a play on the words in the title "Open Harbor: Is it? Within Reach" with crossing out "is it?" with "It IS!" (see attached example) Must include the author's name: Marla Quentin, PhD Must include a smaller tagline: "Practical Steps to Move Teams Forward Again"
• Showing diverse people, or hands. Diverse kinds of groups - not just business. A colorful cover. Maybe show the complexity of trust when it is broken...broken pieces of trust that are then picked up and put together when people work together. Could show people (or images of hands) or other ways to show that it's a choice and it is possible to repair broken trust. I'd also like to convey a sense of a group - not just random people. That they have something at stake to work on repairing trust together and this book can help them.
• If images of people are used, just showing one gender or race is not okay. Nor just binary choices: like an image containing one man and one woman, or one white person and one person of color - otherwise it seems that the book on Open Harbor is about race or gender relations.

```html
<!DOCTYPE html>
<html lang="en">
<head>
<meta charset="utf-8">
<title>Open Harbor — Spine and Front Cover</title>
<link rel="stylesheet" href="https://fonts.googleapis.com/css2?family=Marcellus&display=swap">
<style>
  :root {
    --page-bg: #ffffff;
    --cover-bg: #dde7e7;
    --cover-bg-deep: #d3dfe0;
    --spine-bg: #2a6580;
    --spine-edge: #1f5570;
    --spine-text: #e8eff0;
    --title-teal: #2f6b84;
    --tagline-navy: #1f3a5c;
    --reach-navy: #1b1f5e;
    --strike-red: #d42a2a;
    --photo-top: #b8c6cc;
    --photo-mid: #5d6f82;
    --photo-low: #2c3a57;
  }
  * { box-sizing: border-box; margin: 0; padding: 0; }
  html, body {
    width: 1200px; height: 1200px; overflow: hidden;
    background: var(--page-bg);
  }
  .book {
    position: absolute;
    left: 252px; top: 60px;
    width: 696px; height: 1080px;
    display: flex;
    font-family: "Marcellus", "Optima", serif;
  }

  /* Spine */
  .spine {
    width: 56px; height: 100%;
    background: linear-gradient(90deg, var(--spine-edge) 0%, var(--spine-bg) 40%, var(--spine-bg) 100%);
    color: var(--spine-text);
    writing-mode: vertical-rl;
    display: flex;
    align-items: center;
    padding: 58px 0 40px;
    text-transform: uppercase;
    white-space: nowrap;
  }
  .spine-title { font-size: 25px; letter-spacing: 0.06em; }
  .spine-wordplay {
    display: flex; flex-direction: row-reverse;
    font-size: 9px; line-height: 10px;
    margin: 0 6px 0 8px;
  }
  .spine-wordplay .correction { transform: translateY(2px); }
  .spine-reach { font-size: 25px; letter-spacing: 0.06em; }
  .spine-author {
    margin-top: auto;
    font-size: 14px; letter-spacing: 0.12em;
  }

  /* Front cover */
  .cover {
    position: relative;
    width: 640px; height: 100%;
    background: linear-gradient(180deg, var(--cover-bg) 0%, var(--cover-bg-deep) 100%);
    text-align: center;
  }
  .tagline {
    position: absolute; left: 0; right: 0; top: 32px;
    color: var(--tagline-navy);
    font-size: 18px; line-height: 25px;
    letter-spacing: 0.22em;
    text-transform: uppercase;
  }
  .title {
    position: absolute; left: 0; right: 0; top: 100px;
    color: var(--title-teal);
    font-size: 118px; line-height: 101px;
    letter-spacing: 0.05em;
    font-weight: 400;
    text-transform: uppercase;
  }
  .title span { display: block; }
  .wordplay {
    position: absolute; left: 0; right: 0; top: 330px;
    color: var(--reach-navy);
    font-size: 22px; line-height: 26px;
  }
  .wordplay .correction {
    display: block;
    transform: translateX(10px) rotate(-6deg);
    letter-spacing: 0.02em;
  }
  .wordplay .question { display: block; letter-spacing: 0.04em; }
  .struck { position: relative; display: inline-block; }
  .struck::before, .struck::after {
    content: ""; position: absolute;
    left: -2px; right: -2px; top: 50%;
    height: 2px; background: var(--strike-red);
  }
  .struck::before { transform: rotate(28deg); }
  .struck::after { transform: rotate(-28deg); }
  .spine .struck::before, .spine .struck::after { height: 1px; }
  .subtitle {
    position: absolute; left: 0; right: 0; top: 392px;
    color: var(--reach-navy);
    font-size: 64px; line-height: 72px;
    letter-spacing: 0.03em;
    text-transform: uppercase;
  }
  .group-photo {
    position: absolute;
    left: 134px; top: 470px;
    width: 430px; height: 496px;
    border-radius: 48% 48% 46% 46%;
    background: radial-gradient(circle at 50% 50%, var(--photo-top) 0%, var(--photo-mid) 45%, var(--photo-low) 100%);
  }
  .author {
    position: absolute; left: 0; right: 0; top: 996px;
    color: var(--title-teal);
    font-size: 30px; line-height: 36px;
    letter-spacing: 0.06em;
  }
</style>
</head>
<body>
  <div class="book">
    <aside class="spine">
      <span class="spine-title">Open Harbor</span>
      <span class="spine-wordplay">
        <span class="correction">IT IS</span>
        <span class="question">IS <span class="struck">IT</span>?</span>
      </span>
      <span class="spine-reach">Within Reach</span>
      <span class="spine-author">Marla Quentin, Ph.D.</span>
    </aside>
    <main class="cover">
      <p class="tagline">Practical Steps to Move<br>Teams Forward Again</p>
      <h1 class="title"><span>Open</span><span>Harbor</span></h1>
      <p class="wordplay">
        <span class="correction">IT IS</span>
        <span class="question">IS <span class="struck">IT</span>?</span>
      </p>
      <p class="subtitle">Within Reach</p>
      <div class="group-photo" role="img" aria-label="Overhead photo of a diverse group of people standing in a circle with their hands joined in the middle"></div>
      <p class="author">MARLA QUENTIN, Ph.D.</p>
    </main>
  </div>
</body>
</html>
```